Celvara Health Group Presentation Folder, for Cancer Awareness, VERY COLORFUL AND MODERN

Presentation Folder I know pretty much what i want so it should be very eazy , I have included files from folders I use now rebrand them to my new company they will be fine, no sense re creating the wheel
Full Bleed Size
20.87" x 16.68"
53 x 42.4 cm
6260 x 5004 pixels
Document Trim Size
20.75" x 16.56"
52.7 x 42.1 cm
6225 x 4969 pixels

Low design quality

Industry/Entity Type

Medical

Font styles to use
Serif

Colors

Designer to choose colors to be used in the design.

Requirements
Must have
• really I am not looking for some one to redesign, we like our folder front page and would like to see new word information added., there are two folder front pages to choose from
• So Keep the original front page and redesign the back page and the pockets
• Can Make your Design off of one of the ones I already uploaded
Nice to have
• Keep the same color schemes, Keep the original front page and redesign the back page and the pockets
Should not have
• DO not recreate the front covers, use what I gave you and just rebrand

```html
<!DOCTYPE html>
<html lang="en">
<head>
<meta charset="utf-8">
<title>Celvara Health Group – Presentation Folder</title>
<link rel="stylesheet" href="https://fonts.googleapis.com/css2?family=Raleway:wght@400;500;600;700&display=swap">
<style>
  :root{
    --page:#ececec;
    --paper:#ffffff;
    --green:#c8e2a4;
    --navy:#1f2f6e;
    --navy-dark:#0f1f5c;
    --pink:#e8728a;
    --sky:#55bfe6;
    --frame:#9fd6f0;
    --grey-strip:#d3d3d3;
    --grey-soft:#f3f3f3;
    --body:#555a66;
    --cut:#e8554f;
  }
  *{box-sizing:border-box;margin:0;padding:0}
  html,body{width:902px;height:1200px;overflow:hidden;background:var(--page);font-family:"Raleway",sans-serif}
  .folder{position:absolute;left:18px;top:254px;width:866px;height:692px;background:var(--paper)}
  .folder-shapes{position:absolute;inset:0}
  .panel{position:absolute;top:14px;width:375px;height:476px;border:1px solid var(--frame)}
  .panel--inside-left{left:46px}
  .panel--inside-right{left:447px}

  .family-photo{position:absolute;left:62px;top:30px;width:250px;height:250px;border-radius:50%;
    background:radial-gradient(circle at 50% 40%,#f3e4d6 0%,#d9b59a 55%,#a9826a 100%)}
  .intro{position:absolute;left:14px;top:298px;width:347px;font-size:10.4px;line-height:1.3;color:var(--body);text-align:justify}
  .intro strong{color:var(--pink);font-weight:600}
  .motto{position:absolute;left:14px;top:390px;width:347px;text-align:center;font-weight:700}
  .motto-lead{color:var(--pink);font-size:12.5px;margin-bottom:3px}
  .motto-body{color:#3d4d8f;font-size:12.5px;line-height:1.36}

  .headline{position:absolute;left:0;top:32px;width:100%;text-align:center;color:var(--pink);font-size:21px;font-weight:700;letter-spacing:.2px}
  .subhead{position:absolute;left:0;top:63px;width:100%;text-align:center;color:var(--navy);font-size:9.6px;font-weight:700}
  .mission{position:absolute;left:28px;top:88px;width:320px;text-align:center;color:var(--sky);font-size:8.6px;line-height:1.35;text-transform:uppercase}
  .dinner-photo{position:absolute;left:28px;top:190px;width:322px;height:200px;transform:rotate(3deg);
    border:5px solid #fff;box-shadow:3px 4px 8px rgba(0,0,0,.35);
    background:linear-gradient(160deg,#f4efe6 0%,#d8c3a5 45%,#a88e74 100%)}
  .tagline{position:absolute;left:14px;top:438px;display:flex;align-items:center;gap:12px;color:var(--navy);font-size:15px;font-weight:500}
  .tagline-mark{width:32px;height:32px;border-radius:50%;background:var(--navy)}

  .pocket-label{position:absolute;transform:rotate(180deg);text-align:center}
  .pocket-label--left{left:130px;top:520px;width:220px}
  .pocket-label--left .name{color:var(--pink);font-size:16px;font-weight:500;letter-spacing:.5px}
  .pocket-label--left .division{color:#8a8fa6;font-size:9.5px}
  .pocket-label--right{left:560px;top:560px;display:flex;align-items:center;gap:12px}
  .pocket-label--right .name{color:var(--navy-dark);font-size:20px;font-weight:700;line-height:1.05;text-align:left;width:110px}
  .pocket-label--right .mark{width:60px;height:60px;border-radius:50%;background:var(--navy-dark)}
</style>
</head>
<body>
<div class="folder">
  <svg class="folder-shapes" width="866" height="692" viewBox="0 0 866 692">
    <!-- side flaps -->
    <path d="M0 2 L32 0 V505 L0 497 Z" fill="var(--green)"/>
    <path d="M834 0 L866 2 V497 L834 505 Z" fill="var(--green)"/>
    <circle cx="0" cy="315" r="14" fill="#fff" stroke="var(--cut)" stroke-width=".8"/>
    <circle cx="866" cy="315" r="14" fill="#fff" stroke="var(--cut)" stroke-width=".8"/>
    <!-- fold lines -->
    <line x1="433" y1="2" x2="433" y2="505" stroke="#8cc08c" stroke-width="1" stroke-dasharray="3 3"/>
    <line x1="32" y1="505" x2="834" y2="505" stroke="#8cc08c" stroke-width="1" stroke-dasharray="3 3"/>
    <!-- left pocket -->
    <path d="M34 505 H432 L406 678 Q403 692 390 692 H34 Z" fill="var(--green)" stroke="var(--cut)" stroke-width=".8"/>
    <rect x="34" y="505" width="26" height="187" fill="var(--grey-strip)"/>
    <path d="M60 505 H418 L410 560 Q360 680 210 692 H60 Z" fill="var(--grey-soft)"/>
    <g stroke="var(--cut)" stroke-width="1">
      <line x1="155" y1="580" x2="180" y2="556"/><line x1="282" y1="556" x2="307" y2="580"/>
      <line x1="155" y1="620" x2="180" y2="644"/><line x1="282" y1="644" x2="307" y2="620"/>
    </g>
    <!-- right pocket -->
    <clipPath id="right-pocket"><path d="M436 505 H834 V692 H480 Q467 692 464 678 Z"/></clipPath>
    <g clip-path="url(#right-pocket)">
      <rect x="430" y="505" width="410" height="190" fill="var(--green)"/>
      <circle cx="705" cy="520" r="190" fill="#fff"/>
      <rect x="806" y="505" width="28" height="190" fill="var(--grey-strip)"/>
    </g>
    <path d="M436 505 H834 V692 H480 Q467 692 464 678 Z" fill="none" stroke="var(--cut)" stroke-width=".8"/>
    <path d="M457 518 H799 V678 H478 Q470 678 468 668 Z" fill="none" stroke="var(--frame)" stroke-width="1"/>
  </svg>

  <section class="panel panel--inside-left">
    <div class="family-photo" role="img" aria-label="Photo of a smiling three-generation family framed in a circle"></div>
    <p class="intro"><strong>Hereditary cancer screening</strong> provides vital information to help people with a strong personal or family history of cancer understand their own risk of developing the disease. With this information, they can take steps to Potentially Prevent Cancer, Delay the Onset of Cancer or Catch it at an Earlier stage when outcomes and survival rates are Better.</p>
    <div class="motto">
      <p class="motto-lead">Don’t be Afraid of the Answer:</p>
      <p class="motto-body">Knowledge is Power and Power Eradicates Fear.<br>When You are Fearless, You Will Make all the<br>Right Choices!</p>
    </div>
  </section>

  <section class="panel panel--inside-right">
    <h1 class="headline">HEREDITARY CANCER SCREENING</h1>
    <p class="subhead">DOCTORS ARE THE GATEKEEPERS TO GENETIC TESTING.</p>
    <p class="mission">We have an obligation to help patients understand genetic risk and how testing can guide heath care decisions.</p>
    <div class="dinner-photo" role="img" aria-label="Photo of a family sharing a meal at an outdoor table"></div>
    <p class="tagline"><span class="tagline-mark"></span>The test you order FOR your patients</p>
  </section>

  <div class="pocket-label pocket-label--left">
    <p class="name">CELVARA HEALTH GROUP</p>
    <p class="division">a division of Norwell Medical Sales LLC</p>
  </div>
  <div class="pocket-label pocket-label--right">
    <span class="mark"></span>
    <p class="name">CELVARA HEALTH GROUP</p>
  </div>
</div>
</body>
</html>
```